Birch And Harbor Website A Website design for book editing

A website design for book editing

Our proofreading, editing and manuscript review packages are specifically tailored to help you publish the best possible version of your story.

NEED HELP PUBLISHING A BESTSELLER?

If you’re looking for professional book editing services from senior publishing industry insiders, look no further. Besides editing, we can also answer all your publishing questions and get you started building your author platform.

OUR SERVICES

We've carefully structured our packages to maximize value for every budget.

PRICING

$.02
PER WORD
Proofreading
Line Edit (Copy-editing)
Fix spelling and grammar
Sales copy/summary revision

$.04
PER WORD
Proofreading
Line Edit (Copy-editing)
Fix spelling and grammar
Organization and content
Plot and pacing
Manuscript Review

$.06
PER WORD
Proofreading
Line Edit (Copy-editing)
Fix spelling and grammar
Organization and content
Plot and pacing
Manuscript Review
Formatting (print and ebook)
Pre-publication proofread

OUR PROCESS

Send us a sample of your book. Our caffeine-fueled, eagle-eyed editors will go through it and then email you with their comments and suggestions. You can ask them any questions you want. They will look for…

Typos and grammatical errors.
Spelling and word choice issues
Punctuation and style
Word choice, clarity and flow.
Sentence structure and craft
If your writing is already clean, then they’ll discuss bigger picture things with you, like theme, concept, purpose, audience, potential market and branding (including title, subtitle, and tagline or elevator pitch).

Once you feel comfortable and confident in an editor’s expertise, skill and knowledge, and are ready to move ahead, we’ll send an invoice for the first half of the total word count so the editor can get started. We’ll charge the rest when the project is close to completion.

Target Market(s)

Authors

Industry/Entity Type

Book Publisher

Coding

Coded - Design and coding required

Number of Pages Required

1 page

Requirements
Must have
• OUR SERVICES
• We've carefully structured our packages to maximize value for every budget.
• PRICING
• $.02
• PER WORD
• Proofreading
• Line Edit (Copy-editing)
• Fix spelling and grammar
• Sales copy/summary revision
• $.04
• PER WORD
• Proofreading
• Organization and content
• Plot and pacing
• Manuscript Review
• $.06
• PER WORD
• Proofreading
• Plot and pacing
• Manuscript Review
• Formatting (print and ebook)
• Pre-publication proofread

```html
<!DOCTYPE html>
<html lang="en">
<head>
<meta charset="utf-8">
<title>Birch And Harbor – Book Editing</title>
<link href="https://fonts.googleapis.com/css2?family=Lato:wght@400;700;900&family=Open+Sans:wght@400;600;700&display=swap" rel="stylesheet">
<style>
:root{
  --red:#d7001c;
  --ink:#1b1b1b;
  --text:#555;
  --muted:#777;
  --line:#cfcfcf;
  --soft:#f4f4f4;
  --bar:#7d7d7d;
  --white:#fff;
}
*{margin:0;padding:0;box-sizing:border-box}
html,body{width:1200px;height:3523px;overflow:hidden}
body{position:relative;background:var(--white);font-family:'Open Sans',sans-serif;color:var(--text)}
.abs{position:absolute}

/* header */
.site-header{left:0;top:0;width:1200px;height:104px;background:var(--white)}
.brand{left:98px;top:34px;display:flex;align-items:center;gap:12px;font-family:'Lato',sans-serif;font-weight:900;font-size:34px;color:var(--red)}
.brand-dot{width:16px;height:16px;border-radius:50%;background:var(--red)}
.call{right:98px;top:16px;font-family:'Lato',sans-serif;font-weight:900;font-size:15px;color:var(--ink);display:flex;align-items:center;gap:8px}
.call strong{color:var(--red);font-size:22px}
.main-nav{right:98px;top:62px;display:flex;gap:30px;font-family:'Lato',sans-serif;font-weight:900;font-size:16px;color:var(--ink);align-items:center}
.main-nav .active{color:var(--red)}

/* hero */
.hero{left:0;top:104px;width:1200px;height:551px;background:linear-gradient(100deg,#1e1e1e 0%,#4a4a4a 35%,#9a9a98 65%,#c9c9c6 100%)}
.hero-title{left:0;top:236px;width:1200px;text-align:center;font-family:'Lato',sans-serif;font-weight:900;font-size:62px;line-height:74px;color:var(--white);letter-spacing:1px}
.btn-solid{left:508px;top:418px;width:184px;height:58px;border-radius:29px;background:var(--red);color:var(--white);font-family:'Lato',sans-serif;font-weight:900;font-size:16px;display:flex;align-items:center;justify-content:center}
.dots{left:562px;top:591px;display:flex;gap:5px}
.dots span{width:14px;height:14px;border-radius:50%;border:2px solid var(--white)}
.dots span.on{background:var(--white)}

/* welcome */
.welcome-box{left:98px;top:728px;width:602px;height:406px;border:2px solid var(--line);padding:36px 135px 0 32px}
.welcome-box h2{font-family:'Lato',sans-serif;font-weight:900;font-size:36px;line-height:46px;color:var(--ink)}
.welcome-box h2 span{color:var(--red)}
.welcome-box p{margin-top:32px;font-size:13.5px;line-height:30px;color:var(--text);width:430px}
.btn-outline{height:44px;border:2px solid var(--red);border-radius:22px;color:var(--red);font-family:'Lato',sans-serif;font-weight:900;font-size:15px;display:flex;align-items:center;justify-content:center}
.welcome-box .btn-outline{position:absolute;left:32px;top:316px;width:132px}
.welcome-media{left:618px;top:765px;width:483px;height:329px;background:linear-gradient(135deg,#e9e7e4 0%,#d6d2cd 50%,#b9b3ac 100%)}
.play{left:828px;top:898px;width:62px;height:62px;border-radius:50%;background:#222;border:3px solid var(--white)}

/* services */
.services{left:0;top:1221px;width:1200px;height:676px;background:var(--soft)}
.section-title{width:1200px;left:0;text-align:center;font-family:'Lato',sans-serif;font-weight:900;font-size:38px;color:var(--ink)}
.section-title span{color:var(--red)}
.section-sub{left:0;width:1200px;text-align:center;font-size:15px;color:var(--text)}
.service-card{width:413px;height:172px;border:2px solid var(--line);background:var(--soft)}
.service-card h3{font-family:'Lato',sans-serif;font-weight:700;font-size:21px;color:var(--ink);margin-top:18px}
.service-card p{font-size:13px;line-height:22px;color:var(--text);margin-top:12px}
.service-card .more{position:absolute;bottom:14px;font-family:'Lato',sans-serif;font-weight:900;font-size:13px;color:var(--red)}
.card-left{padding-left:36px;padding-right:100px;text-align:left}
.card-left h3{text-align:center;padding-left:40px}
.card-left .more{right:100px}
.card-right{padding-left:100px;padding-right:30px}
.card-right .more{left:100px}
.icon-ring{width:130px;height:130px;border-radius:50%;border:2px solid var(--line);background:var(--soft);display:flex;align-items:center;justify-content:center}

/* pricing */
.price-card{top:2050px;width:318px;border:2px solid #ddd;background:var(--white);box-shadow:0 2px 6px rgba(0,0,0,.12)}
.price-card h3{height:58px;line-height:58px;text-align:center;font-family:'Lato',sans-serif;font-weight:700;font-size:26px;color:var(--ink)}
.price-bar{height:59px;background:var(--bar);color:var(--white);text-align:center;font-family:'Lato',sans-serif;font-weight:900;font-size:38px;line-height:59px}
.price-bar small{font-family:'Open Sans',sans-serif;font-weight:400;font-size:13px}
.features{list-style:none;padding:28px 0 0 36px}
.features li{font-size:14px;line-height:33px;color:var(--text);display:flex;align-items:center;gap:12px}
.btn-sign{margin:20px auto 36px;width:110px}

/* process */
.process-photo{left:0;top:2691px;width:601px;height:512px;background:linear-gradient(120deg,#e8e5e0 0%,#bdb5aa 45%,#6f655b 80%,#3c3530 100%)}
.process{left:601px;top:2691px;width:599px;height:512px;background:var(--red);color:var(--white);padding:42px 50px 0 48px}
.process h2{font-family:'Lato',sans-serif;font-weight:900;font-size:34px}
.process p{margin-top:22px;font-size:13.5px;line-height:29px}
.checks{list-style:none;margin-top:18px}
.checks li{font-weight:700;font-size:15px;line-height:34px;display:flex;align-items:center;gap:14px}
.process .btn-outline{border-color:var(--white);color:var(--white);width:148px;height:50px;border-radius:25px;margin-top:22px}

/* footer */
.social{left:0;top:3287px;width:1200px;display:flex;justify-content:center;gap:14px}
.social span{width:52px;height:52px;border-radius:50%;border:2px solid #333}
.contact-line{left:0;top:3370px;width:1200px;display:flex;justify-content:center;gap:14px;align-items:center;font-size:13.5px;color:#444}
.legal{left:0;top:3411px;width:1200px;text-align:center;font-size:13.5px;color:#444;word-spacing:2px}
.copy{left:0;top:3446px;width:1200px;text-align:center;font-size:13.5px;color:#444}
</style>
</head>
<body>

<header class="site-header abs">
  <div class="brand abs"><span class="brand-dot"></span>Birch And Harbor</div>
  <div class="call abs">
    <svg width="14" height="14" viewBox="0 0 24 24"><path fill="#d7001c" d="M6.6 10.8a15 15 0 0 0 6.6 6.6l2.2-2.2c.3-.3.7-.4 1-.2 1.1.4 2.3.6 3.6.6.6 0 1 .4 1 1V20c0 .6-.4 1-1 1A17 17 0 0 1 3 4c0-.6.4-1 1-1h3.5c.6 0 1 .4 1 1 0 1.3.2 2.5.6 3.6.1.3 0 .7-.2 1z"/></svg>
    CALL US ON : <strong>1 555 204 7716</strong>
  </div>
  <nav class="main-nav abs">
    <span class="active">HOME</span><span>ABOUT US</span><span>SERVICES</span><span>PROCESS</span><span>BLOG</span><span>TOOLS</span><span>CONTACT</span>
    <svg width="16" height="16" viewBox="0 0 24 24"><circle cx="10" cy="10" r="7" fill="none" stroke="#1b1b1b" stroke-width="3"/><path d="M15 15l6 6" stroke="#1b1b1b" stroke-width="3"/></svg>
  </nav>
</header>

<section class="hero abs" role="img" aria-label="Writer working at a desk with notebook, pen and keyboard"></section>
<h1 class="hero-title abs">NEED HELP PUBLISHING<br>A BESTSELLER?</h1>
<div class="btn-solid abs">GET STARTED</div>
<div class="dots abs"><span class="on"></span><span></span><span></span><span></span></div>

<div class="welcome-media abs" role="img" aria-label="Hand marking a manuscript page with a red pen"></div>
<svg class="play abs" viewBox="0 0 62 62"><path d="M24 18l20 13-20 13z" fill="#fff"/></svg>
<section class="welcome-box abs">
  <h2>WELCOME TO<br><span>BIRCH AND HARBOR</span></h2>
  <p>Since our first season we have paired writers with seasoned editors who read every line with care. We sharpen voice, tighten structure and guide each draft toward print, so your finished book reads cleanly and lands the way you always imagined it would on the page.</p>
  <div class="btn-outline">READ MORE</div>
</section>

<section class="services abs"></section>
<h2 class="section-title abs" style="top:1286px">OUR <span>SERVICES</span></h2>
<p class="section-sub abs" style="top:1349px">We've carefully structured our packages to maximize value for every budget.</p>

<article class="service-card card-left abs" style="left:98px;top:1428px">
  <h3>Developmental Editing</h3>
  <p>Big-picture guidance on structure, character arcs and pacing so your story holds together.</p>
  <span class="more">READ MORE</span>
</article>
<article class="service-card card-right abs" style="left:688px;top:1428px">
  <h3>Manuscript Critique</h3>
  <p>A detailed reader report on strengths, weak spots and clear next steps for revision.</p>
  <span class="more">READ MORE</span>
</article>
<article class="service-card card-left abs" style="left:98px;top:1641px">
  <h3>Comprehensive Edit</h3>
  <p>A full pass on content and line level prose that leaves each chapter polished.</p>
  <span class="more">READ MORE</span>
</article>
<article class="service-card card-right abs" style="left:688px;top:1641px">
  <h3>Copyediting</h3>
  <p>Careful correction of grammar, spelling, punctuation and consistency across the manuscript.</p>
  <span class="more">READ MORE</span>
</article>

<div class="icon-ring abs" style="left:447px;top:1449px">
  <svg width="66" height="60" viewBox="0 0 66 60" fill="#d7001c"><circle cx="24" cy="32" r="14"/><g stroke="#d7001c" stroke-width="7"><path d="M24 12v40M4 32h40M10 18l28 28M38 18L10 46"/></g><circle cx="24" cy="32" r="6" fill="#f4f4f4"/><circle cx="50" cy="16" r="8"/><g stroke="#d7001c" stroke-width="4"><path d="M50 4v24M38 16h24M42 8l16 16M58 8L42 24"/></g><circle cx="50" cy="16" r="3" fill="#f4f4f4"/><circle cx="52" cy="46" r="6"/><g stroke="#d7001c" stroke-width="3"><path d="M52 37v18M43 46h18"/></g><circle cx="52" cy="46" r="2" fill="#f4f4f4"/></svg>
</div>
<div class="icon-ring abs" style="left:623px;top:1449px">
  <svg width="48" height="60" viewBox="0 0 48 60"><path d="M2 2h30l14 14v42H2z" fill="#d7001c"/><path d="M32 2v14h14" fill="#f4a0a8"/><g stroke="#fff" stroke-width="3"><path d="M10 28h28M10 36h28M10 44h28"/></g></svg>
</div>
<div class="icon-ring abs" style="left:447px;top:1662px">
  <svg width="60" height="60" viewBox="0 0 60 60" fill="none" stroke="#d7001c" stroke-width="5"><path d="M40 8H10a4 4 0 0 0-4 4v38a4 4 0 0 0 4 4h38a4 4 0 0 0 4-4V24"/><path d="M50 4l6 6-26 26-9 3 3-9z" fill="#d7001c"/></svg>
</div>
<div class="icon-ring abs" style="left:623px;top:1662px">
  <svg width="60" height="60" viewBox="0 0 60 60" fill="none" stroke="#d7001c" stroke-width="4"><path d="M4 6h20l8 8v30H4z"/><path d="M24 18h20l10 10v28H24z" fill="#f4f4f4"/><path d="M44 18v10h10"/></svg>
</div>

<h2 class="section-title abs" style="top:1962px">PRICING <span>PLAN</span></h2>

<article class="price-card abs" style="left:98px">
  <h3>SILVER</h3>
  <div class="price-bar">$.02 <small>Per Word</small></div>
  <ul class="features">
    <li><svg width="13" height="11" viewBox="0 0 13 11"><path d="M1 6l4 4 7-9" fill="none" stroke="#d7001c" stroke-width="2.5"/></svg>Proofreading</li>
    <li><svg width="13" height="11" viewBox="0 0 13 11"><path d="M1 6l4 4 7-9" fill="none" stroke="#d7001c" stroke-width="2.5"/></svg>Line Edit (Copy-editing)</li>
    <li><svg width="13" height="11" viewBox="0 0 13 11"><path d="M1 6l4 4 7-9" fill="none" stroke="#d7001c" stroke-width="2.5"/></svg>Fix spelling and grammar</li>
    <li><svg width="13" height="11" viewBox="0 0 13 11"><path d="M1 6l4 4 7-9" fill="none" stroke="#d7001c" stroke-width="2.5"/></svg>Sales copy/summary revision</li>
  </ul>
  <div class="btn-outline btn-sign">SIGN UP</div>
</article>

<article class="price-card abs" style="left:441px">
  <h3>GOLD</h3>
  <div class="price-bar">$.04 <small>Per Word</small></div>
  <ul class="features">
    <li><svg width="13" height="11" viewBox="0 0 13 11"><path d="M1 6l4 4 7-9" fill="none" stroke="#d7001c" stroke-width="2.5"/></svg>Proofreading</li>
    <li><svg width="13" height="11" viewBox="0 0 13 11"><path d="M1 6l4 4 7-9" fill="none" stroke="#d7001c" stroke-width="2.5"/></svg>Line Edit (Copy-editing)</li>
    <li><svg width="13" height="11" viewBox="0 0 13 11"><path d="M1 6l4 4 7-9" fill="none" stroke="#d7001c" stroke-width="2.5"/></svg>Fix spelling and grammar</li>
    <li><svg width="13" height="11" viewBox="0 0 13 11"><path d="M1 6l4 4 7-9" fill="none" stroke="#d7001c" stroke-width="2.5"/></svg>Sales copy/summary revision</li>
    <li><svg width="13" height="11" viewBox="0 0 13 11"><path d="M1 6l4 4 7-9" fill="none" stroke="#d7001c" stroke-width="2.5"/></svg>Organization and content</li>
    <li><svg width="13" height="11" viewBox="0 0 13 11"><path d="M1 6l4 4 7-9" fill="none" stroke="#d7001c" stroke-width="2.5"/></svg>Plot and pacing</li>
    <li><svg width="13" height="11" viewBox="0 0 13 11"><path d="M1 6l4 4 7-9" fill="none" stroke="#d7001c" stroke-width="2.5"/></svg>Manuscript Review</li>
  </ul>
  <div class="btn-outline btn-sign">SIGN UP</div>
</article>

<article class="price-card abs" style="left:784px">
  <h3>SILVER</h3>
  <div class="price-bar">$.06 <small>Per Word</small></div>
  <ul class="features">
    <li><svg width="13" height="11" viewBox="0 0 13 11"><path d="M1 6l4 4 7-9" fill="none" stroke="#d7001c" stroke-width="2.5"/></svg>Proofreading</li>
    <li><svg width="13" height="11" viewBox="0 0 13 11"><path d="M1 6l4 4 7-9" fill="none" stroke="#d7001c" stroke-width="2.5"/></svg>Line Edit (Copy-editing)</li>
    <li><svg width="13" height="11" viewBox="0 0 13 11"><path d="M1 6l4 4 7-9" fill="none" stroke="#d7001c" stroke-width="2.5"/></svg>Fix spelling and grammar</li>
    <li><svg width="13" height="11" viewBox="0 0 13 11"><path d="M1 6l4 4 7-9" fill="none" stroke="#d7001c" stroke-width="2.5"/></svg>Sales copy/summary revision</li>
    <li><svg width="13" height="11" viewBox="0 0 13 11"><path d="M1 6l4 4 7-9" fill="none" stroke="#d7001c" stroke-width="2.5"/></svg>Organization and content</li>
    <li><svg width="13" height="11" viewBox="0 0 13 11"><path d="M1 6l4 4 7-9" fill="none" stroke="#d7001c" stroke-width="2.5"/></svg>Plot and pacing</li>
    <li><svg width="13" height="11" viewBox="0 0 13 11"><path d="M1 6l4 4 7-9" fill="none" stroke="#d7001c" stroke-width="2.5"/></svg>Manuscript Review</li>
    <li><svg width="13" height="11" viewBox="0 0 13 11"><path d="M1 6l4 4 7-9" fill="none" stroke="#d7001c" stroke-width="2.5"/></svg>Formatting (print and ebook)</li>
    <li><svg width="13" height="11" viewBox="0 0 13 11"><path d="M1 6l4 4 7-9" fill="none" stroke="#d7001c" stroke-width="2.5"/></svg>Pre-publication proofread</li>
  </ul>
  <div class="btn-outline btn-sign">SIGN UP</div>
</article>

<div class="process-photo abs" role="img" aria-label="Hand holding a pen over printed manuscript pages"></div>
<section class="process abs">
  <h2>OUR PROCESS</h2>
  <p>Send us a sample of your book. Our caffeine-fueled, eagle-eyed editors will go through it and then email you with their comments and suggestions. You can ask them any questions you want. They will look for…</p>
  <ul class="checks">
    <li><svg width="18" height="18" viewBox="0 0 18 18"><circle cx="9" cy="9" r="9" fill="#fff"/><path d="M5 9l3 3 5-6" fill="none" stroke="#d7001c" stroke-width="2.2"/></svg>Typos and grammatical errors.</li>
    <li><svg width="18" height="18" viewBox="0 0 18 18"><circle cx="9" cy="9" r="9" fill="#fff"/><path d="M5 9l3 3 5-6" fill="none" stroke="#d7001c" stroke-width="2.2"/></svg>Spelling and word choice issues</li>
    <li><svg width="18" height="18" viewBox="0 0 18 18"><circle cx="9" cy="9" r="9" fill="#fff"/><path d="M5 9l3 3 5-6" fill="none" stroke="#d7001c" stroke-width="2.2"/></svg>Punctuation and style</li>
    <li><svg width="18" height="18" viewBox="0 0 18 18"><circle cx="9" cy="9" r="9" fill="#fff"/><path d="M5 9l3 3 5-6" fill="none" stroke="#d7001c" stroke-width="2.2"/></svg>Word choice, clarity and flow.</li>
    <li><svg width="18" height="18" viewBox="0 0 18 18"><circle cx="9" cy="9" r="9" fill="#fff"/><path d="M5 9l3 3 5-6" fill="none" stroke="#d7001c" stroke-width="2.2"/></svg>Sentence structure and craft</li>
  </ul>
  <div class="btn-outline">GET STARTED</div>
</section>

<footer>
  <div class="social abs"><span></span><span></span><span></span><span></span></div>
  <div class="contact-line abs">
    <svg width="12" height="16" viewBox="0 0 12 16"><path d="M6 0a6 6 0 0 1 6 6c0 4-6 10-6 10S0 10 0 6a6 6 0 0 1 6-6z" fill="#d7001c"/><circle cx="6" cy="6" r="2" fill="#fff"/></svg>
    <span>412 Alder Row , Suite 210, Fairmont Hills,GA</span><span>|</span>
    <svg width="14" height="14" viewBox="0 0 24 24"><path fill="#d7001c" d="M6.6 10.8a15 15 0 0 0 6.6 6.6l2.2-2.2c.3-.3.7-.4 1-.2 1.1.4 2.3.6 3.6.6.6 0 1 .4 1 1V20c0 .6-.4 1-1 1A17 17 0 0 1 3 4c0-.6.4-1 1-1h3.5c.6 0 1 .4 1 1 0 1.3.2 2.5.6 3.6.1.3 0 .7-.2 1z"/></svg>
    <span>1 555 204 7716</span><span>|</span>
    <svg width="16" height="12" viewBox="0 0 16 12"><rect width="16" height="12" rx="1" fill="#d7001c"/><path d="M1 1l7 6 7-6" fill="none" stroke="#fff" stroke-width="1.4"/></svg>
    <span>info@birchandharbor.com</span>
  </div>
  <div class="legal abs">Help &nbsp;|&nbsp; FAQ &nbsp;|&nbsp; Support &nbsp;|&nbsp; Sitemap &nbsp;|&nbsp; Terms Of Use &nbsp;|&nbsp; Privacy Statement</div>
  <div class="copy abs">Copyrights © 2018, Birch And Harbor. All rights reserved.</div>
</footer>

</body>
</html>
```